Alterations to existing business card

Here is my current logo and I want the "cafe and bar" taken off with just the words Lumo and our slogan "Savour the moment" on the card, Plus the logo.
Our Current Business Card is currently 5.5cm by 5.5cm and would like it to remain like this thanks.
The loyalty card can be 10 squares with the logo specifying the 10th coffee free. I would like the cheapest option please.
Also on our business card would like the Facebook logo and instagram Logo with TAZALUMO27 as link to our photos on instagram.

Keep Colour schemes the same please.

On the business cards

Dale Brinton Director
0427916038
dale27lumo@mailvista.test

Paula Ferrisi Principal
0428571963
paulumo@mailvista.test

Thanks Dale

Industry/Entity Type

Business

```html
<!DOCTYPE html>
<html lang="en">
<head>
<meta charset="utf-8">
<title>Lumo business and loyalty cards</title>
<link rel="stylesheet" href="https://fonts.googleapis.com/css2?family=Questrial&display=swap">
<style>
  :root {
    --stage: #4b4b4b;
    --white: #ffffff;
    --ink: #151515;
    --orange: #eea73c;
    --gold-light: #f8e27a;
    --gold-mid: #f3c250;
    --shadow: rgba(0,0,0,0.35);
  }
  * { margin: 0; padding: 0; box-sizing: border-box; }
  html, body { width: 1105px; height: 1200px; overflow: hidden; }
  body {
    background: var(--stage);
    font-family: "Questrial", "Century Gothic", sans-serif;
    position: relative;
  }
  .card {
    position: absolute;
    width: 449px;
    height: 449px;
    box-shadow: 0 4px 10px var(--shadow);
    overflow: hidden;
  }

  /* Business card */
  .business-card { left: 124px; top: 110px; background: var(--white); }
  .business-card .top-band {
    position: absolute; left: 0; top: 0; width: 100%; height: 120px;
    background: linear-gradient(90deg, var(--orange), var(--gold-mid) 55%, var(--gold-light));
  }
  .business-card .bottom-band {
    position: absolute; left: 0; bottom: 0; width: 100%; height: 14px; background: var(--ink);
  }
  .business-card .mark { position: absolute; left: 148px; top: 37px; }
  .brand-name {
    position: absolute; left: 0; width: 100%; top: 180px;
    text-align: center; font-size: 64px; font-weight: 400; letter-spacing: 2px; color: var(--ink); line-height: 1;
  }
  .slogan {
    position: absolute; left: 0; width: 100%; top: 246px;
    text-align: center; font-size: 14px; font-style: italic; letter-spacing: 1px; color: var(--orange); line-height: 1;
  }
  .person-name {
    position: absolute; left: 0; width: 100%; top: 280px;
    text-align: center; font-size: 27px; font-weight: 400; letter-spacing: 1px; color: var(--orange);
  }
  .role {
    position: absolute; left: 0; width: 100%; top: 313px;
    display: flex; justify-content: center; align-items: center; gap: 6px;
    font-size: 18px; letter-spacing: 1px; color: var(--ink);
  }
  .role .rule { width: 56px; height: 1px; background: var(--ink); }
  .contact {
    position: absolute; left: 0; width: 100%;
    display: flex; justify-content: center; align-items: center; gap: 6px;
    font-size: 20px; color: #333;
  }
  .contact.phone { top: 354px; }
  .contact.email { top: 383px; }

  /* Loyalty card */
  .loyalty-card {
    left: 500px; top: 630px;
    background: linear-gradient(90deg, var(--orange), var(--gold-mid) 55%, var(--gold-light));
  }
  .loyalty-card .mark { position: absolute; left: 133px; top: 31px; }
  .stamps { position: absolute; left: 0; top: 0; }
  .handle-row {
    position: absolute; left: 0; width: 100%; top: 397px;
    display: flex; justify-content: center; align-items: center; gap: 8px;
    font-size: 19px; letter-spacing: 1px; color: var(--ink);
  }
  .handle-row .rule { width: 82px; height: 1px; background: var(--ink); }
  .handle-row .dot { width: 16px; height: 16px; border-radius: 50%; background: var(--ink); }
</style>
</head>
<body>

<section class="card business-card" aria-label="Lumo business card">
  <div class="top-band"></div>
  <svg class="mark" width="152" height="152" viewBox="0 0 152 152" aria-hidden="true">
    <circle cx="76" cy="76" r="74" fill="var(--white)"/>
    <circle cx="76" cy="76" r="64" fill="none" stroke="var(--orange)" stroke-width="4"/>
  </svg>
  <h1 class="brand-name">LUMO</h1>
  <p class="slogan">SAVOUR THE MOMENT</p>
  <h2 class="person-name">DALE BRINTON</h2>
  <p class="role"><span class="rule"></span>DIRECTOR<span class="rule"></span></p>
  <p class="contact phone">
    <svg width="14" height="22" viewBox="0 0 14 22" aria-hidden="true">
      <rect x="1" y="1" width="12" height="20" rx="2" fill="none" stroke="var(--orange)" stroke-width="2"/>
      <circle cx="7" cy="17" r="1.3" fill="var(--orange)"/>
    </svg>
    0427916038
  </p>
  <p class="contact email">
    <svg width="18" height="13" viewBox="0 0 18 13" aria-hidden="true">
      <rect x="0" y="0" width="18" height="13" fill="var(--orange)"/>
      <path d="M1 1 L9 7 L17 1" fill="none" stroke="var(--white)" stroke-width="1.5"/>
    </svg>
    dale27lumo@mailvista.test
  </p>
  <div class="bottom-band"></div>
</section>

<section class="card loyalty-card" aria-label="Lumo loyalty card">
  <svg class="mark" width="170" height="170" viewBox="0 0 170 170" aria-hidden="true">
    <circle cx="85" cy="85" r="80" fill="none" stroke="var(--ink)" stroke-width="4"/>
    <text x="85" y="98" text-anchor="middle" font-family="Questrial, sans-serif" font-size="40" letter-spacing="2" fill="var(--ink)">LUMO</text>
  </svg>

  <svg class="stamps" width="449" height="449" viewBox="0 0 449 449" aria-label="Ten coffee stamps, the tenth free">
    <defs>
      <g id="stamp-ring">
        <circle r="32" fill="none" stroke="var(--ink)" stroke-width="2.5"/>
        <circle r="27" fill="none" stroke="var(--ink)" stroke-width="1.5"/>
      </g>
      <g id="cup">
        <path d="M-13 -4 H9 V4 A9 9 0 0 1 0 12 H-4 A9 9 0 0 1 -13 4 Z" fill="var(--ink)"/>
        <path d="M9 -1 A5 5 0 0 1 9 8" fill="none" stroke="var(--ink)" stroke-width="2.5"/>
        <rect x="-17" y="13" width="30" height="2.5" rx="1.2" fill="var(--ink)"/>
        <path d="M-6 -8 q-3 -4 0 -8 M-1 -8 q-3 -4 0 -8" fill="none" stroke="var(--ink)" stroke-width="1.6"/>
      </g>
    </defs>
    <g transform="translate(76,256)"><use href="#stamp-ring"/><use href="#cup"/></g>
    <g transform="translate(147,256)"><use href="#stamp-ring"/><use href="#cup"/></g>
    <g transform="translate(218,256)"><use href="#stamp-ring"/><use href="#cup"/></g>
    <g transform="translate(289,256)"><use href="#stamp-ring"/><use href="#cup"/></g>
    <g transform="translate(364,256)"><use href="#stamp-ring"/><use href="#cup"/></g>
    <g transform="translate(76,337)"><use href="#stamp-ring"/><use href="#cup"/></g>
    <g transform="translate(147,337)"><use href="#stamp-ring"/><use href="#cup"/></g>
    <g transform="translate(218,337)"><use href="#stamp-ring"/><use href="#cup"/></g>
    <g transform="translate(289,337)"><use href="#stamp-ring"/><use href="#cup"/></g>
    <g transform="translate(364,337)">
      <circle r="32" fill="var(--orange)"/>
      <use href="#stamp-ring"/>
      <text y="7" text-anchor="middle" font-family="Questrial, sans-serif" font-size="19" font-weight="700" fill="var(--ink)">FREE</text>
    </g>
  </svg>

  <p class="handle-row"><span class="rule"></span><span class="dot"></span>TAZALUMO27<span class="rule"></span></p>
</section>

</body>
</html>
```